Quillmarsh Property Solutions need a business card design

Hello guys. We would need a business card design asap please.
We are a start up property investment business based in London UK specialised in buying, selling, managing and letting properties and helping distressed property owners.
The name of our Business is Quillmarsh, the logo symbolises the four fundamental elements of the world (earth, air, fire and water) and so it stands for strength, stability, longevity.
We would like the business card to communicate professionalism and reliability. Many many thanks indeed for your work.

Details:

1.) Rosalind Updike
Property Investor
Mobile: +44(0)7700123456
Email: rosalind.quillmarsh@mailbox-example.com

2.) Dominic Updike
Property Investor
Mobile: +44(0)7700987654
Email: dominic.quillmarsh@mailbox-example.com

```html
<!DOCTYPE html>
<html lang="en">
<head>
<meta charset="utf-8">
<title>Quillmarsh Property Solutions – Business Card</title>
<link rel="stylesheet" href="https://fonts.googleapis.com/css2?family=Open+Sans:wght@400;600;700&display=swap">
<style>
  :root {
    --backdrop: #d9dadc;
    --card: #ffffff;
    --ink: #111111;
    --ink-soft: #9a9a9a;
    --band-red: #e3232f;
    --band-green: #1f9d3a;
    --band-blue: #2f6fc4;
    --shadow: rgba(0, 0, 0, 0.16);
  }
  * { box-sizing: border-box; margin: 0; padding: 0; }
  html, body { width: 1200px; height: 800px; overflow: hidden; }
  body {
    background: var(--backdrop);
    font-family: "Open Sans", Arial, sans-serif;
    position: relative;
  }
  .card {
    position: absolute;
    top: 257px;
    width: 500px;
    height: 286px;
    background: var(--card);
    box-shadow: 0 6px 18px var(--shadow);
    overflow: hidden;
  }
  .card--back { left: 60px; }
  .card--front { left: 640px; }

  /* Back: name mark centered */
  .brand-mark {
    position: absolute;
    display: flex;
    align-items: center;
    gap: 16px;
  }
  .card--back .brand-mark { left: 120px; top: 112px; }
  .brand-mark__square {
    width: 34px; height: 34px;
    background: var(--band-green);
  }
  .brand-mark__name {
    font-weight: 600;
    color: var(--ink-soft);
    text-transform: uppercase;
    line-height: 1.15;
    font-size: 20px;
    letter-spacing: 1px;
  }
  .brand-mark__name span { display: block; }

  /* Front */
  .card--front .brand-mark { left: 40px; top: 52px; gap: 10px; }
  .card--front .brand-mark__square { width: 22px; height: 22px; }
  .card--front .brand-mark__name {
    color: var(--ink);
    font-size: 15px;
    letter-spacing: 0.5px;
  }
  .contact {
    position: absolute;
    left: 330px;
    top: 118px;
    color: var(--ink);
    font-size: 11px;
    line-height: 1.35;
  }
  .contact__name { font-size: 18px; font-weight: 400; margin-bottom: 3px; }
  .band {
    position: absolute;
    left: 0; bottom: 0;
    width: 100%;
    height: 14px;
    display: flex;
  }
  .band__seg { flex: 1; }
  .band__seg--red { background: var(--band-red); }
  .band__seg--green { background: var(--band-green); }
  .band__seg--blue { background: var(--band-blue); }
</style>
</head>
<body>
  <section class="card card--back" aria-label="Business card back">
    <div class="brand-mark">
      <div class="brand-mark__square"></div>
      <p class="brand-mark__name"><span>Quillmarsh</span><span>Property Solutions</span></p>
    </div>
  </section>

  <section class="card card--front" aria-label="Business card front">
    <div class="brand-mark">
      <div class="brand-mark__square"></div>
      <p class="brand-mark__name"><span>Quillmarsh</span><span>Property Solutions</span></p>
    </div>
    <div class="contact">
      <p class="contact__name">Alden Pryce</p>
      <p>Director</p>
      <p>Phone:(555) 014-2287</p>
      <p>118 Fenwick Row</p>
      <p>Harlow Bend, ST</p>
      <p>(Stateland) 00417</p>
    </div>
    <div class="band">
      <div class="band__seg band__seg--red"></div>
      <div class="band__seg band__seg--green"></div>
      <div class="band__seg band__seg--blue"></div>
      <div class="band__seg band__seg--red"></div>
      <div class="band__seg band__seg--green"></div>
    </div>
  </section>
</body>
</html>
```